Design a Brazilian children's Bible calendar for 2017

We need someone to design a children's calendar for 2017 with an animal theme.
The format is 21cm x 15cm and we need the front cover and one page with two months as can be seen in the attached files.
Target Market(s)
Brazilian children
Font styles to use
Sans Serif
Requirements
Must have
- Modern, clean design

```html
<!DOCTYPE html>
<html lang="pt-BR">
<head>
<meta charset="utf-8">
<title>2017 Children's Bible Calendar</title>
<link href="https://fonts.googleapis.com/css2?family=Montserrat:wght@700;800&family=Quicksand:wght@500;700&display=swap" rel="stylesheet">
<style>
:root{
  --board-grey:#cbc3c2;
  --paper:#ffffff;
  --gold:#e9b61f;
  --coral:#e3785f;
  --slate-blue:#6b8bb6;
  --lavender:#ae92b3;
  --rose:#f3a19f;
  --sun:#f6c65a;
  --meadow:#8bbf5c;
  --ink-white:#ffffff;
  --verse-blue:#3b4f7c;
}
*{margin:0;padding:0;box-sizing:border-box}
html,body{width:1200px;height:2571px;overflow:hidden}
body{
  position:relative;
  background:linear-gradient(var(--board-grey) 0 1242px,var(--paper) 1242px);
  font-family:"Quicksand",sans-serif;
}
.cover{
  position:absolute;left:213px;top:125px;width:757px;height:1075px;
  background:var(--paper);overflow:hidden;
}
.cover-photo{
  position:absolute;inset:0;
  background:
    radial-gradient(ellipse 210px 260px at 50% 70%,#b8733a 0 55%,rgba(184,115,58,0) 100%),
    linear-gradient(#ffffff 0 30%,#e3ead5 40%,#a9c983 54%,#7fb458 70%,#73a94c 100%);
}
.title-name{
  position:absolute;left:0;right:0;text-align:center;
  font-family:"Montserrat",sans-serif;font-weight:700;color:var(--gold);line-height:1.1;
}
.title-name span{display:block}
.cover .title-name{top:135px}
.cover .title-name .big{font-size:96px}
.cover .title-name .small{font-size:34px;margin-top:20px}

.page{position:absolute;width:382px;height:532px;overflow:hidden}
.page-photo{height:232px}
.page-panel{height:300px;position:relative;color:var(--ink-white)}
.title-art{
  position:absolute;left:50%;top:38px;width:240px;height:50px;margin-left:-120px;
  border-radius:6px;
}
.panel-year{
  position:absolute;left:0;right:0;top:58px;text-align:center;
  font-family:"Montserrat",sans-serif;font-weight:800;font-size:26px;line-height:26px;
}
.verse{
  position:absolute;left:26px;right:26px;top:102px;text-align:center;
  font-family:"Montserrat",sans-serif;font-weight:700;font-size:10px;line-height:11px;
}
.verse cite{display:block;font-style:normal;font-size:7px;line-height:11px}
.months{
  position:absolute;left:18px;right:18px;top:135px;
  display:flex;justify-content:space-between;
}
.month{width:158px}
.month h3{
  font-weight:500;font-size:21px;line-height:24px;text-align:center;margin-bottom:5px;
}
.weekdays,.days{display:grid;grid-template-columns:repeat(7,1fr);list-style:none}
.weekdays li{
  width:16px;height:16px;border-radius:50%;background:var(--ink-white);
  font-family:"Montserrat",sans-serif;font-weight:700;font-size:4px;line-height:16px;text-align:center;
  margin:0 auto 6px;
}
.days li{
  font-family:"Quicksand",sans-serif;font-weight:700;font-size:11px;line-height:13px;text-align:center;
}
.s0 li:first-child{grid-column-start:1}
.s1 li:first-child{grid-column-start:2}
.s2 li:first-child{grid-column-start:3}
.s3 li:first-child{grid-column-start:4}
.s4 li:first-child{grid-column-start:5}
.s5 li:first-child{grid-column-start:6}
.s6 li:first-child{grid-column-start:7}

.col-a{left:19px}.col-b{left:411px}.col-c{left:800px}
.row-a{top:1270px}.row-b{top:1817px}

.page--coral .page-panel{background:var(--coral)}
.page--coral .weekdays li{color:var(--coral)}
.page--blue .page-panel{background:var(--slate-blue)}
.page--blue .weekdays li{color:var(--slate-blue)}
.page--lavender .page-panel{background:var(--lavender)}
.page--lavender .weekdays li{color:var(--lavender)}
.page--rose .page-panel{background:var(--rose)}
.page--rose .weekdays li{color:var(--rose)}
.page--sun .page-panel{background:var(--sun)}
.page--sun .weekdays li{color:var(--sun)}
.page--meadow .page-panel{background:var(--meadow)}
.page--meadow .weekdays li{color:var(--meadow)}

.page--coral .panel-year,.page--coral .verse{color:var(--verse-blue)}
.page--blue .panel-year{color:#e66a8a}.page--blue .verse{color:#f06b8c}
.page--lavender .panel-year,.page--lavender .verse{color:#6a2a7c}
.page--rose .panel-year{color:#f2c230}.page--rose .verse{color:#3f3f58}
.page--sun .panel-year,.page--sun .verse{color:#7a5a1c}
.page--meadow .panel-year{color:#c2304a}.page--meadow .verse{color:#c2304a}

.footer-name{top:2402px}
.footer-name .big{font-size:50px}
.footer-name .small{font-size:18px;margin-top:8px}
</style>
</head>
<body>

<section class="cover">
  <div class="cover-photo" role="img" aria-label="Photo of a small brown spaniel puppy sitting in green grass"></div>
  <h1 class="title-name"><span class="big">2017</span><span class="small">children's bible calendar</span></h1>
</section>

<article class="page page--coral col-a row-a">
  <div class="page-photo" role="img" aria-label="Photo of a black and white puppy lying on sand with a ball" style="background:linear-gradient(#6e6a55 0 12%,#d9d2c7 30%,#e6e0d6 100%)"></div>
  <div class="page-panel">
    <div class="title-art" role="img" aria-label="Illustration of grass, flowers, a dog and a bird" style="background:linear-gradient(#e3785f 0 40%,#5f9a45 40%)"></div>
    <span class="panel-year">2017</span>
    <p class="verse">No princípio, criou Deus os céus e a terra<cite>Gênesis 1:1</cite></p>
    <div class="months">
      <div class="month"><h3>Janeiro</h3>
        <ul class="weekdays"><li>DOM</li><li>SEG</li><li>TER</li><li>QUA</li><li>QUI</li><li>SEX</li><li>SÁB</li></ul>
        <ol class="days s0"><li>1</li><li>2</li><li>3</li><li>4</li><li>5</li><li>6</li><li>7</li><li>8</li><li>9</li><li>10</li><li>11</li><li>12</li><li>13</li><li>14</li><li>15</li><li>16</li><li>17</li><li>18</li><li>19</li><li>20</li><li>21</li><li>22</li><li>23</li><li>24</li><li>25</li><li>26</li><li>27</li><li>28</li><li>29</li><li>30</li><li>31</li></ol>
      </div>
      <div class="month"><h3>Fevereiro</h3>
        <ul class="weekdays"><li>DOM</li><li>SEG</li><li>TER</li><li>QUA</li><li>QUI</li><li>SEX</li><li>SÁB</li></ul>
        <ol class="days s3"><li>1</li><li>2</li><li>3</li><li>4</li><li>5</li><li>6</li><li>7</li><li>8</li><li>9</li><li>10</li><li>11</li><li>12</li><li>13</li><li>14</li><li>15</li><li>16</li><li>17</li><li>18</li><li>19</li><li>20</li><li>21</li><li>22</li><li>23</li><li>24</li><li>25</li><li>26</li><li>27</li><li>28</li></ol>
      </div>
    </div>
  </div>
</article>

<article class="page page--blue col-b row-a">
  <div class="page-photo" role="img" aria-label="Photo of a seagull standing by the sea" style="background:linear-gradient(#eef1f2 0 55%,#3f88b5 62%,#5a6f7c 100%)"></div>
  <div class="page-panel">
    <div class="title-art" role="img" aria-label="Illustration of a boat on waves and a flying seagull" style="background:linear-gradient(#6b8bb6 0 60%,#4d72a3 60%)"></div>
    <span class="panel-year">2017</span>
    <p class="verse">Lorem ipsum dolor sit amet czonsectetuer adipiscing elit aenean commodo<cite>Lorem Ipsum</cite></p>
    <div class="months">
      <div class="month"><h3>Julho</h3>
        <ul class="weekdays"><li>DOM</li><li>SEG</li><li>TER</li><li>QUA</li><li>QUI</li><li>SEX</li><li>SÁB</li></ul>
        <ol class="days s6"><li>1</li><li>2</li><li>3</li><li>4</li><li>5</li><li>6</li><li>7</li><li>8</li><li>9</li><li>10</li><li>11</li><li>12</li><li>13</li><li>14</li><li>15</li><li>16</li><li>17</li><li>18</li><li>19</li><li>20</li><li>21</li><li>22</li><li>23</li><li>24</li><li>25</li><li>26</li><li>27</li><li>28</li><li>29</li><li>30</li><li>31</li></ol>
      </div>
      <div class="month"><h3>Agosto</h3>
        <ul class="weekdays"><li>DOM</li><li>SEG</li><li>TER</li><li>QUA</li><li>QUI</li><li>SEX</li><li>SÁB</li></ul>
        <ol class="days s2"><li>1</li><li>2</li><li>3</li><li>4</li><li>5</li><li>6</li><li>7</li><li>8</li><li>9</li><li>10</li><li>11</li><li>12</li><li>13</li><li>14</li><li>15</li><li>16</li><li>17</li><li>18</li><li>19</li><li>20</li><li>21</li><li>22</li><li>23</li><li>24</li><li>25</li><li>26</li><li>27</li><li>28</li><li>29</li><li>30</li><li>31</li></ol>
      </div>
    </div>
  </div>
</article>

<article class="page page--lavender col-c row-a">
  <div class="page-photo" role="img" aria-label="Photo of a barn owl among yellow wildflowers" style="background:linear-gradient(#6e6a3e 0%,#c9a93a 45%,#e8c63c 70%,#8a8a3e 100%)"></div>
  <div class="page-panel">
    <div class="title-art" role="img" aria-label="Illustration of wildflowers and a small owl" style="background:linear-gradient(#ae92b3 0 50%,#9c9a5c 50%)"></div>
    <span class="panel-year">2017</span>
    <p class="verse">Lorem ipsum dolor sit amet czonsectetuer adipiscing elit aenean commodo<cite>Lorem Ipsum</cite></p>
    <div class="months">
      <div class="month"><h3>Setembro</h3>
        <ul class="weekdays"><li>DOM</li><li>SEG</li><li>TER</li><li>QUA</li><li>QUI</li><li>SEX</li><li>SÁB</li></ul>
        <ol class="days s5"><li>1</li><li>2</li><li>3</li><li>4</li><li>5</li><li>6</li><li>7</li><li>8</li><li>9</li><li>10</li><li>11</li><li>12</li><li>13</li><li>14</li><li>15</li><li>16</li><li>17</li><li>18</li><li>19</li><li>20</li><li>21</li><li>22</li><li>23</li><li>24</li><li>25</li><li>26</li><li>27</li><li>28</li><li>29</li><li>30</li></ol>
      </div>
      <div class="month"><h3>Outubro</h3>
        <ul class="weekdays"><li>DOM</li><li>SEG</li><li>TER</li><li>QUA</li><li>QUI</li><li>SEX</li><li>SÁB</li></ul>
        <ol class="days s0"><li>1</li><li>2</li><li>3</li><li>4</li><li>5</li><li>6</li><li>7</li><li>8</li><li>9</li><li>10</li><li>11</li><li>12</li><li>13</li><li>14</li><li>15</li><li>16</li><li>17</li><li>18</li><li>19</li><li>20</li><li>21</li><li>22</li><li>23</li><li>24</li><li>25</li><li>26</li><li>27</li><li>28</li><li>29</li><li>30</li><li>31</li></ol>
      </div>
    </div>
  </div>
</article>

<article class="page page--rose col-a row-b">
  <div class="page-photo" role="img" aria-label="Photo of a white and tabby cat lying on a wooden floor" style="background:linear-gradient(#4d4a46 0%,#8a8580 45%,#b3aca5 70%,#6a645e 100%)"></div>
  <div class="page-panel">
    <div class="title-art" role="img" aria-label="Illustration of a cat on grass under a night sky with a moon" style="background:linear-gradient(#444055 0 60%,#4f9a3c 60%)"></div>
    <span class="panel-year">2017</span>
    <p class="verse">Lorem ipsum dolor sit amet czonsectetuer adipiscing elit aenean commodo<cite>Lorem Ipsum</cite></p>
    <div class="months">
      <div class="month"><h3>Março</h3>
        <ul class="weekdays"><li>DOM</li><li>SEG</li><li>TER</li><li>QUA</li><li>QUI</li><li>SEX</li><li>SÁB</li></ul>
        <ol class="days s3"><li>1</li><li>2</li><li>3</li><li>4</li><li>5</li><li>6</li><li>7</li><li>8</li><li>9</li><li>10</li><li>11</li><li>12</li><li>13</li><li>14</li><li>15</li><li>16</li><li>17</li><li>18</li><li>19</li><li>20</li><li>21</li><li>22</li><li>23</li><li>24</li><li>25</li><li>26</li><li>27</li><li>28</li><li>29</li><li>30</li><li>31</li></ol>
      </div>
      <div class="month"><h3>Abril</h3>
        <ul class="weekdays"><li>DOM</li><li>SEG</li><li>TER</li><li>QUA</li><li>QUI</li><li>SEX</li><li>SÁB</li></ul>
        <ol class="days s6"><li>1</li><li>2</li><li>3</li><li>4</li><li>5</li><li>6</li><li>7</li><li>8</li><li>9</li><li>10</li><li>11</li><li>12</li><li>13</li><li>14</li><li>15</li><li>16</li><li>17</li><li>18</li><li>19</li><li>20</li><li>21</li><li>22</li><li>23</li><li>24</li><li>25</li><li>26</li><li>27</li><li>28</li><li>29</li><li>30</li></ol>
      </div>
    </div>
  </div>
</article>

<article class="page page--sun col-b row-b">
  <div class="page-photo" role="img" aria-label="Photo of a giraffe in front of green trees" style="background:linear-gradient(#d8dcd8 0 8%,#5f7d4e 30%,#4e6a3e 70%,#6b8654 100%)"></div>
  <div class="page-panel">
    <div class="title-art" role="img" aria-label="Illustration of a giraffe, bushes and birds" style="background:linear-gradient(#f6c65a 0 50%,#e8a93a 50%)"></div>
    <span class="panel-year">2017</span>
    <p class="verse">Lorem ipsum dolor sit amet czonsectetuer adipiscing elit aenean commodo<cite>Lorem Ipsum</cite></p>
    <div class="months">
      <div class="month"><h3>Maio</h3>
        <ul class="weekdays"><li>DOM</li><li>SEG</li><li>TER</li><li>QUA</li><li>QUI</li><li>SEX</li><li>SÁB</li></ul>
        <ol class="days s1"><li>1</li><li>2</li><li>3</li><li>4</li><li>5</li><li>6</li><li>7</li><li>8</li><li>9</li><li>10</li><li>11</li><li>12</li><li>13</li><li>14</li><li>15</li><li>16</li><li>17</li><li>18</li><li>19</li><li>20</li><li>21</li><li>22</li><li>23</li><li>24</li><li>25</li><li>26</li><li>27</li><li>28</li><li>29</li><li>30</li><li>31</li></ol>
      </div>
      <div class="month"><h3>Junho</h3>
        <ul class="weekdays"><li>DOM</li><li>SEG</li><li>TER</li><li>QUA</li><li>QUI</li><li>SEX</li><li>SÁB</li></ul>
        <ol class="days s4"><li>1</li><li>2</li><li>3</li><li>4</li><li>5</li><li>6</li><li>7</li><li>8</li><li>9</li><li>10</li><li>11</li><li>12</li><li>13</li><li>14</li><li>15</li><li>16</li><li>17</li><li>18</li><li>19</li><li>20</li><li>21</li><li>22</li><li>23</li><li>24</li><li>25</li><li>26</li><li>27</li><li>28</li><li>29</li><li>30</li></ol>
      </div>
    </div>
  </div>
</article>

<article class="page page--meadow col-c row-b">
  <div class="page-photo" role="img" aria-label="Photo of a deer standing on a grassy hill" style="background:linear-gradient(#a9b3b8 0 25%,#3f5a78 45%,#3e4a38 70%,#2e3a28 100%)"></div>
  <div class="page-panel">
    <div class="title-art" role="img" aria-label="Illustration of a reindeer, pine trees and a Christmas tree with gifts" style="background:linear-gradient(#8bbf5c 0 45%,#3f7a3a 45%)"></div>
    <span class="panel-year">2017</span>
    <p class="verse">Lorem ipsum dolor sit amet czonsectetuer adipiscing elit aenean commodo<cite>Lorem Ipsum</cite></p>
    <div class="months">
      <div class="month"><h3>Novembro</h3>
        <ul class="weekdays"><li>DOM</li><li>SEG</li><li>TER</li><li>QUA</li><li>QUI</li><li>SEX</li><li>SÁB</li></ul>
        <ol class="days s3"><li>1</li><li>2</li><li>3</li><li>4</li><li>5</li><li>6</li><li>7</li><li>8</li><li>9</li><li>10</li><li>11</li><li>12</li><li>13</li><li>14</li><li>15</li><li>16</li><li>17</li><li>18</li><li>19</li><li>20</li><li>21</li><li>22</li><li>23</li><li>24</li><li>25</li><li>26</li><li>27</li><li>28</li><li>29</li><li>30</li></ol>
      </div>
      <div class="month"><h3>Dezembro</h3>
        <ul class="weekdays"><li>DOM</li><li>SEG</li><li>TER</li><li>QUA</li><li>QUI</li><li>SEX</li><li>SÁB</li></ul>
        <ol class="days s5"><li>1</li><li>2</li><li>3</li><li>4</li><li>5</li><li>6</li><li>7</li><li>8</li><li>9</li><li>10</li><li>11</li><li>12</li><li>13</li><li>14</li><li>15</li><li>16</li><li>17</li><li>18</li><li>19</li><li>20</li><li>21</li><li>22</li><li>23</li><li>24</li><li>25</li><li>26</li><li>27</li><li>28</li><li>29</li><li>30</li><li>31</li></ol>
      </div>
    </div>
  </div>
</article>

<footer class="title-name footer-name"><span class="big">2017</span><span class="small">children's bible calendar</span></footer>

</body>
</html>
```